Trailer Lettering or Partial Wrap

I purchased a new gloss black 7' wide x 12' long x 7' height enclosed cargo trailer that I would like to brand for advertising. on all 4 sides. Our font is AgencyFB (and we only use lower case letters). To reduce cost I thought using the black gloss background could be achieved and use cut out vinyl rather than full wrap unless there are some other ideas. Our colors are Black, White, and Red (HEX #BE1E2D. Items to be displayed:
- logo
- phone # (405) 555-2716
- email. catering@kelpcornerok.com
- web address: www.kelpcornerok.com
- our 2 restaurant locations
- "Edmond" 4875 NE 92nd, Edmond OK 73099
- "NW-OKC" 2719 E Larkspur Ave, Oklahoma City, OK 73198

we would also like to highlight 3 services we offer:
- Catering
- Rent-A-Chef Events
- Sushi Making Classes

For reference our chopsticks from the logo files we use on a lot of print items. Not that I want it to be like this, but I did attach a sample of what ChatGPT created though is in an unusable format and fonts aren't consistent. As well a recent 2' x 4' sign we had made to use on table displays.

We also do like the wording on that last item of " Sushi | Experience | Elevated"

```html
<!DOCTYPE html>
<html lang="en">
<head>
<meta charset="utf-8">
<title>Kelp Corner — Trailer Graphics</title>
<link href="https://fonts.googleapis.com/css2?family=Saira+Condensed:wght@400;600&display=swap" rel="stylesheet">
<style>
:root{
  --black:#0d0d0d;
  --panel:#151515;
  --white:#ffffff;
  --red:#be1e2d;
  --grey:#2a2a2a;
  --stage:#e9ebee;
  --font:"Saira Condensed", "Arial Narrow", sans-serif;
}
*{margin:0;padding:0;box-sizing:border-box}
html,body{width:1200px;height:3889px;overflow:hidden;background:var(--stage)}
body{position:relative;font-family:var(--font);color:var(--white)}
.view{position:absolute;left:0;width:1200px;height:972px}
.panel{position:absolute;background:var(--panel);overflow:hidden;border-radius:4px}
.abs{position:absolute}
.enso-white{position:absolute;border-radius:50%;background:radial-gradient(circle,#fff 70%,#d9d9d9 100%)}
.enso-dark{position:absolute;border-radius:50%;background:radial-gradient(circle,rgba(255,255,255,0) 62%,rgba(255,255,255,.09) 72%,rgba(255,255,255,0) 80%)}
.waves{position:absolute;background:linear-gradient(180deg,#202020,#2b2b2b);opacity:.8}
.brand{position:absolute;color:var(--black);font-weight:600;line-height:.86;text-transform:lowercase;letter-spacing:-1px}
.brand-round{position:absolute;border-radius:50%;background:var(--white);display:flex;align-items:center;justify-content:center}
.brand-round .brand{position:static;font-size:58px;text-align:left}
.icon{position:absolute;border-radius:50%;background:radial-gradient(circle,#fff 0 38%,var(--black) 39% 64%,var(--red) 65%)}
.service{position:absolute;font-size:44px;line-height:1;white-space:nowrap}
.rule{position:absolute;height:2px;background:var(--red)}
.svc-label{position:absolute;width:150px;text-align:center;font-size:27px;line-height:1;color:#ddd;transform:translateX(-50%)}
.contact{position:absolute;text-align:center;transform:translateX(-50%);white-space:nowrap;line-height:1.1}
.loc{color:var(--red);font-size:28px;display:flex;align-items:center;justify-content:center;gap:4px}
.addr{font-size:16px;color:#eee}
.line{font-size:21px;display:flex;align-items:center;justify-content:center;gap:6px}
.divider{position:absolute;width:2px;background:var(--red)}
.web{position:absolute;background:var(--red);border-radius:30px;display:flex;align-items:center;justify-content:center;color:var(--white);white-space:nowrap}
svg.ic{fill:var(--red)}
.big .loc{font-size:42px}
.big .addr{font-size:25px}
.big .line{font-size:35px}
</style>
</head>
<body>
<svg width="0" height="0" style="position:absolute">
  <defs>
    <symbol id="pin" viewBox="0 0 24 24"><path d="M12 1a8 8 0 0 0-8 8c0 6 8 14 8 14s8-8 8-14a8 8 0 0 0-8-8zm0 11a3 3 0 1 1 0-6 3 3 0 0 1 0 6z"/></symbol>
    <symbol id="mail" viewBox="0 0 24 24"><circle cx="12" cy="12" r="12"/><rect x="5.5" y="7.5" width="13" height="9" fill="#fff"/><path d="M5.5 7.5l6.5 5 6.5-5" fill="none" stroke="#be1e2d" stroke-width="1.4"/></symbol>
    <symbol id="phone" viewBox="0 0 24 24"><circle cx="12" cy="12" r="12"/><path d="M8 6c1 0 2 2.5 2 3s-1 1-1 1.5c.5 1.5 2 3 3.5 3.5.5 0 1-1 1.5-1s3 1 3 2-1.5 2.5-2.5 2.5C10 17.5 6.5 14 6.5 8.5 6.5 7.5 7 6 8 6z" fill="#fff"/></symbol>
  </defs>
</svg>

<!-- Street side -->
<section class="view" style="top:0">
  <div class="panel" style="left:72px;top:136px;width:1027px;height:649px">
    <div class="enso-white" role="img" aria-label="Brush-stroke ink circle" style="left:584px;top:-60px;width:588px;height:588px"></div>
    <div class="waves" role="img" aria-label="Wave pattern" style="left:20px;top:560px;width:330px;height:89px"></div>
    <div class="brand" style="left:732px;top:110px;font-size:112px">kelp<br>corner</div>
    <div class="icon" role="img" aria-label="Catering cloche icon" style="left:132px;top:40px;width:96px;height:96px"></div>
    <div class="icon" role="img" aria-label="Chef hat icon" style="left:132px;top:144px;width:96px;height:96px"></div>
    <div class="icon" role="img" aria-label="Sushi class icon" style="left:132px;top:251px;width:96px;height:96px"></div>
    <div class="service" style="left:263px;top:88px">Catering</div>
    <div class="rule" style="left:263px;top:140px;width:241px"></div>
    <div class="service" style="left:263px;top:152px">Rent-A-Chef<br>Events</div>
    <div class="rule" style="left:263px;top:245px;width:241px"></div>
    <div class="service" style="left:263px;top:258px">Sushi Making<br>Classes</div>
    <div class="rule" style="left:263px;top:352px;width:241px"></div>
    <div class="contact" style="left:109px;top:412px"><div class="loc"><svg class="ic" width="22" height="22"><use href="#pin"/></svg>NW-OKC</div><div class="addr">2719 E Larkspur Ave<br>Oklahoma City, OK 73198</div></div>
    <div class="divider" style="left:192px;top:412px;height:66px"></div>
    <div class="contact" style="left:335px;top:416px"><div class="line"><svg class="ic" width="16" height="16"><use href="#mail"/></svg>catering@kelpcornerok.com</div><div class="line"><svg class="ic" width="16" height="16"><use href="#phone"/></svg>(405) 555-2716</div></div>
    <div class="divider" style="left:474px;top:412px;height:66px"></div>
    <div class="contact" style="left:554px;top:412px"><div class="loc"><svg class="ic" width="22" height="22"><use href="#pin"/></svg>Edmond</div><div class="addr">4875 NE 92nd<br>Edmond OK 73099</div></div>
    <div class="web" style="left:738px;top:546px;width:208px;height:30px;font-size:20px">www.kelpcornerok.com</div>
  </div>
</section>

<!-- Front -->
<section class="view" style="top:972px">
  <div class="panel" style="left:257px;top:107px;width:686px;height:573px">
    <div class="enso-dark" role="img" aria-label="Brush-stroke ink circle" style="left:60px;top:-200px;width:580px;height:580px"></div>
    <div class="waves" role="img" aria-label="Wave pattern" style="left:0;top:60px;width:150px;height:110px"></div>
    <div class="waves" role="img" aria-label="Wave pattern" style="left:520px;top:490px;width:166px;height:83px"></div>
    <div class="brand-round" style="left:254px;top:27px;width:172px;height:172px"><div class="brand">kelp<br>corner</div></div>
    <div class="icon" role="img" aria-label="Catering cloche icon" style="left:151px;top:239px;width:96px;height:96px"></div>
    <div class="icon" role="img" aria-label="Chef hat icon" style="left:293px;top:239px;width:96px;height:96px"></div>
    <div class="icon" role="img" aria-label="Sushi class icon" style="left:430px;top:239px;width:96px;height:96px"></div>
    <div class="svc-label" style="left:199px;top:348px">Catering</div>
    <div class="svc-label" style="left:341px;top:348px">Rent-A-Chef<br>Events</div>
    <div class="svc-label" style="left:478px;top:348px">Sushi Making<br>Classes</div>
    <div class="contact" style="left:113px;top:428px"><div class="loc"><svg class="ic" width="22" height="22"><use href="#pin"/></svg>Edmond</div><div class="addr">4875 NE 92nd<br>Edmond OK 73099</div></div>
    <div class="divider" style="left:200px;top:430px;height:60px"></div>
    <div class="contact" style="left:341px;top:432px"><div class="line"><svg class="ic" width="16" height="16"><use href="#mail"/></svg>catering@kelpcornerok.com</div><div class="line"><svg class="ic" width="16" height="16"><use href="#phone"/></svg>(405) 555-2716</div></div>
    <div class="divider" style="left:482px;top:430px;height:60px"></div>
    <div class="contact" style="left:566px;top:428px"><div class="loc"><svg class="ic" width="22" height="22"><use href="#pin"/></svg>NW-OKC</div><div class="addr">2719 E Larkspur Ave<br>Oklahoma City, OK 73198</div></div>
    <div class="web" style="left:177px;top:516px;width:332px;height:42px;font-size:30px">www.kelpcornerok.com</div>
  </div>
</section>

<!-- Curb side -->
<section class="view" style="top:1944px">
  <div class="panel big" style="left:98px;top:128px;width:1031px;height:645px">
    <div class="enso-white" role="img" aria-label="Brush-stroke ink circle" style="left:-100px;top:-150px;width:600px;height:600px"></div>
    <div class="waves" role="img" aria-label="Wave pattern" style="left:780px;top:540px;width:251px;height:105px"></div>
    <div class="brand" style="left:110px;top:42px;font-size:124px">kelp<br>corner</div>
    <div class="icon" role="img" aria-label="Catering cloche icon" style="left:529px;top:46px;width:96px;height:96px"></div>
    <div class="icon" role="img" aria-label="Chef hat icon" style="left:529px;top:151px;width:96px;height:96px"></div>
    <div class="icon" role="img" aria-label="Sushi class icon" style="left:529px;top:257px;width:96px;height:96px"></div>
    <div class="service" style="left:661px;top:90px;font-size:46px">Catering</div>
    <div class="rule" style="left:661px;top:147px;width:237px"></div>
    <div class="service" style="left:661px;top:158px;font-size:46px">Rent-A-Chef<br>Events</div>
    <div class="rule" style="left:661px;top:252px;width:237px"></div>
    <div class="service" style="left:661px;top:264px;font-size:46px">Sushi Making<br>Classes</div>
    <div class="rule" style="left:661px;top:358px;width:237px"></div>
    <div class="contact" style="left:174px;top:396px"><div class="loc"><svg class="ic" width="34" height="34"><use href="#pin"/></svg>Edmond</div><div class="addr">4875 NE 92nd<br>Edmond OK 73099</div></div>
    <div class="divider" style="left:287px;top:400px;height:106px"></div>
    <div class="contact" style="left:521px;top:404px"><div class="line"><svg class="ic" width="28" height="28"><use href="#mail"/></svg>catering@kelpcornerok.com</div><div class="line"><svg class="ic" width="28" height="28"><use href="#phone"/></svg>(405) 555-2716</div></div>
    <div class="divider" style="left:760px;top:400px;height:106px"></div>
    <div class="contact" style="left:898px;top:396px"><div class="loc"><svg class="ic" width="34" height="34"><use href="#pin"/></svg>NW-OKC</div><div class="addr">2719 E Larkspur Ave<br>Oklahoma City, OK 73198</div></div>
    <div class="web" style="left:48px;top:554px;width:329px;height:48px;font-size:34px">www.kelpcornerok.com</div>
  </div>
</section>

<!-- Rear doors -->
<section class="view" style="top:2916px">
  <div class="panel" style="left:268px;top:140px;width:664px;height:703px">
    <div class="enso-dark" role="img" aria-label="Brush-stroke ink circle" style="left:50px;top:-120px;width:580px;height:580px"></div>
    <div class="waves" role="img" aria-label="Wave pattern" style="left:0;top:120px;width:150px;height:120px"></div>
    <div class="waves" role="img" aria-label="Wave pattern" style="left:500px;top:610px;width:164px;height:93px"></div>
    <div class="brand-round" style="left:250px;top:84px;width:180px;height:180px"><div class="brand">kelp<br>corner</div></div>
    <div class="icon" role="img" aria-label="Catering cloche icon" style="left:144px;top:346px;width:96px;height:96px"></div>
    <div class="icon" role="img" aria-label="Chef hat icon" style="left:286px;top:346px;width:96px;height:96px"></div>
    <div class="icon" role="img" aria-label="Sushi class icon" style="left:423px;top:346px;width:96px;height:96px"></div>
    <div class="svc-label" style="left:192px;top:458px">Catering</div>
    <div class="svc-label" style="left:334px;top:458px">Rent-A-Chef<br>Events</div>
    <div class="svc-label" style="left:471px;top:458px">Sushi Making<br>Classes</div>
    <div class="contact" style="left:106px;top:532px"><div class="loc"><svg class="ic" width="22" height="22"><use href="#pin"/></svg>Edmond</div><div class="addr">4875 NE 92nd<br>Edmond OK 73099</div></div>
    <div class="divider" style="left:193px;top:534px;height:60px"></div>
    <div class="contact" style="left:334px;top:536px"><div class="line"><svg class="ic" width="16" height="16"><use href="#mail"/></svg>catering@kelpcornerok.com</div><div class="line"><svg class="ic" width="16" height="16"><use href="#phone"/></svg>(405) 555-2716</div></div>
    <div class="divider" style="left:475px;top:534px;height:60px"></div>
    <div class="contact" style="left:559px;top:532px"><div class="loc"><svg class="ic" width="22" height="22"><use href="#pin"/></svg>NW-OKC</div><div class="addr">2719 E Larkspur Ave<br>Oklahoma City, OK 73198</div></div>
    <div class="web" style="left:169px;top:619px;width:332px;height:42px;font-size:30px">www.kelpcornerok.com</div>
  </div>
</section>
</body>
</html>
```